Slide Master for Holloway Engines - A Systematic Hedge Fund

We are looking for someone to produce a theme and slide master for us for our investor presentations. I have uploaded a few examples of templates that we would like to have included:
Main Title
Section Title
Slides with just bullet points
Different image/table configurations with bullet points and foot notes
Biographies of different lengths
A disclaimer (no one will read this but it should still look nice and needs to be in the presentations)
I have also uploaded the company logo, business card and colour definitions. Currently we have a blue colour scheme defined, but it would be nice to get a complementary set of colours so that when we have charts with more elements we can just draw from those.
The most important thing is that the slide master must be of general use to us. We arn't looking to have a specific presentation designed for us, but a theme/style that we can apply ourselves to any presentation we need to give in the future. It should have clearly defined guidelines for where content should go (and if this is different with and without footnotes for example). We would also like it to have a similar feel to the logo/business cards, so matt colours, high contrast, but not busy.
I'm excited to see the results!

```html
<!DOCTYPE html>
<html lang="en">
<head>
<meta charset="utf-8">
<title>Holloway Engines – Slide Master</title>
<link href="https://fonts.googleapis.com/css2?family=Montserrat:wght@600;700;800&family=Lato:wght@400;700&display=swap" rel="stylesheet">
<style>
  :root{
    --navy:#0f2b57;
    --navy-deep:#0a1f3f;
    --blue:#1c4a85;
    --ink:#1d2330;
    --muted:#5a6170;
    --rule:#c9ccd2;
    --page:#f1f1f1;
    --white:#ffffff;
    --sage:#9fc0ae;
  }
  *{box-sizing:border-box;margin:0;padding:0}
  html,body{width:1200px;height:4831px;overflow:hidden;background:var(--page)}
  body{position:relative;font-family:'Lato',sans-serif;color:var(--ink)}
  .slide{position:absolute;left:34px;width:1130px;height:636px;background:var(--white);overflow:hidden;box-shadow:0 1px 4px rgba(0,0,0,.12)}
  .top-bar{position:absolute;left:0;top:0;width:100%;height:8px;background:var(--navy)}
  .brand-tab{position:absolute;right:0;top:0;width:280px;height:82px;background:var(--navy);clip-path:polygon(0 0,100% 0,100% 100%,22% 100%)}
  .brand-tab .wordmark{position:absolute;right:34px;top:22px;width:150px;text-align:center;color:var(--white);font-family:'Montserrat',sans-serif;font-weight:700;font-size:15px;line-height:18px;letter-spacing:1px}
  .photo{position:absolute}
  .slide-title{position:absolute;left:32px;top:30px;font-family:'Montserrat',sans-serif;font-weight:800;font-size:38px;color:var(--navy);letter-spacing:.5px}
  .slide-subtitle{position:absolute;left:32px;top:82px;font-size:15px;font-weight:700;color:var(--ink)}
  .footnote{position:absolute;left:32px;bottom:14px;font-size:9.5px;line-height:17px;color:var(--ink)}
  .footnote.light{color:var(--white)}
  .tick{display:inline-block;width:12px;height:12px;vertical-align:-1px;margin-right:5px}
  .bullets{list-style:none;position:absolute}
  .bullets li{font-size:10px;line-height:24px;color:var(--muted);white-space:nowrap}
  .bullets .tick{width:10px;height:10px}
  .section-head{position:absolute;font-family:'Lato',sans-serif;font-weight:700;font-size:19px;color:var(--navy-deep)}

  /* title slide */
  .cover{top:41px;height:636px;background:#1f2530}
  .cover .photo{inset:0;background:linear-gradient(110deg,#3b3f48 0%,#252a34 45%,#1c2029 70%,#3a3128 100%)}
  .cover .wordmark{position:absolute;left:0;right:0;top:205px;text-align:center;color:var(--white);font-family:'Montserrat',sans-serif;font-weight:700}
  .cover .wordmark .w1{display:block;font-size:56px;letter-spacing:2px;line-height:64px}
  .cover .wordmark .w2{display:block;font-size:30px;letter-spacing:22px;line-height:44px;margin-left:22px}

  /* contents */
  .contents{top:724px}
  .contents .slide-title{top:28px;font-size:36px}
  .toc{list-style:none;position:absolute;left:36px;top:140px;width:1060px}
  .toc li{position:relative;height:66px;display:flex;align-items:center;font-size:17px;color:var(--ink)}
  .toc .label{width:557px}
  .toc .leader{flex:0 0 412px;height:1px;background:var(--rule)}
  .toc .num{position:absolute;left:988px;width:32px;height:32px;border-radius:50%;background:#eceef1;font-weight:700;font-size:14px;display:flex;align-items:center;justify-content:center}

  /* section slide */
  .section{top:1406px;background:var(--navy)}
  .section .photo{inset:0;background:linear-gradient(100deg,#1b3766 0%,#2a4a7c 35%,#213f70 65%,#17305a 100%)}
  .section .headline{position:absolute;left:0;right:0;top:298px;text-align:center;color:var(--white);font-family:'Montserrat',sans-serif;font-weight:700;font-size:27px}

  .bio{top:2091px}
  .charts{top:2773px}
  .lines{top:3456px}
  .chart-card{position:absolute;top:254px;width:492px;height:294px;background:var(--white);border:1px solid #dcdfe3;box-shadow:0 1px 4px rgba(0,0,0,.1)}
  .chart-card .chart-title{position:absolute;top:26px;left:0;right:0;text-align:center;font-size:13px;color:#555}
  .chart-card svg{position:absolute;left:0;top:0}
  .body-copy{position:absolute;left:604px;width:490px;font-size:10.5px;line-height:21px;color:var(--muted)}

  .closing{top:4138px;background:#0b1426}
  .closing .photo{inset:0;background:radial-gradient(ellipse at 50% 60%,#1b2a45 0%,#0d1830 55%,#070e1c 100%)}
  .closing .thanks{position:absolute;left:0;right:0;top:268px;text-align:center;color:var(--white);font-family:'Montserrat',sans-serif;font-weight:800;font-size:92px;letter-spacing:1px}
</style>
</head>
<body>

<svg width="0" height="0" style="position:absolute">
  <defs>
    <symbol id="tick" viewBox="0 0 12 12"><circle cx="6" cy="6" r="6" fill="#1c4a85"/><path d="M3.2 6.2l2 2 3.8-4" fill="none" stroke="#fff" stroke-width="1.6" stroke-linecap="round" stroke-linejoin="round"/></symbol>
  </defs>
</svg>

<!-- Title slide -->
<section class="slide cover">
  <div class="photo" role="img" aria-label="Photograph of a senior businessman at a desk reading a document beside a laptop, dark overlay"></div>
  <div class="wordmark"><span class="w1">HOLLOWAY</span><span class="w2">ENGINES</span></div>
</section>

<!-- Contents -->
<section class="slide contents">
  <div class="top-bar"></div>
  <div class="brand-tab"><div class="wordmark">HOLLOWAY<br>ENGINES</div></div>
  <h1 class="slide-title">SELECT TITLES</h1>
  <ol class="toc">
    <li><span class="label"><svg class="tick"><use href="#tick"/></svg>Lorem ipsum dolor sit amet, consectetur adipiscing elit, sed do</span><span class="leader"></span><span class="num">1</span></li>
    <li><span class="label"><svg class="tick"><use href="#tick"/></svg>Lorem ipsum dolor sit amet, consectetur adipiscing elit, sed do</span><span class="leader"></span><span class="num">2</span></li>
    <li><span class="label"><svg class="tick"><use href="#tick"/></svg>Lorem ipsum dolor sit amet, consectetur adipiscing elit, sed do</span><span class="leader"></span><span class="num">3</span></li>
    <li><span class="label"><svg class="tick"><use href="#tick"/></svg>Lorem ipsum dolor sit amet, consectetur adipiscing elit, sed do</span><span class="leader"></span><span class="num">4</span></li>
    <li><span class="label"><svg class="tick"><use href="#tick"/></svg>Lorem ipsum dolor sit amet, consectetur adipiscing elit, sed do</span><span class="leader"></span><span class="num">5</span></li>
    <li><span class="label"><svg class="tick"><use href="#tick"/></svg>Lorem ipsum dolor sit amet, consectetur adipiscing elit, sed do</span><span class="leader"></span><span class="num">6</span></li>
    <li><span class="label"><svg class="tick"><use href="#tick"/></svg>Lorem ipsum dolor sit amet, consectetur adipiscing elit, sed do</span><span class="leader"></span><span class="num">7</span></li>
  </ol>
</section>

<!-- Section title -->
<section class="slide section">
  <div class="photo" role="img" aria-label="Photograph of smiling businessmen shaking hands in an office, navy overlay"></div>
  <div class="top-bar"></div>
  <div class="brand-tab"><div class="wordmark">HOLLOWAY<br>ENGINES</div></div>
  <h2 class="headline">LOREM IPSUM DOLOR SIT AMET, CONSECTETUR ADIPISCING</h2>
  <p class="footnote light"><sup>*</sup>Lorem ipsum dolor sit amet, consectetur adipiscing elit, sed do eiusmod tempor incididunt ut labore et dolore magna aliqua.<br>Ut enim ad minim veniam, quis nostrud exercitation ullamco laboris</p>
</section>

<!-- Image with bullets -->
<section class="slide bio">
  <div class="top-bar"></div>
  <div class="brand-tab"><div class="wordmark">HOLLOWAY<br>ENGINES</div></div>
  <h2 class="slide-title">LOREM IPSUM</h2>
  <p class="slide-subtitle">LOREM IPSUM DOLOR SIT AMET</p>
  <h3 class="section-head" style="left:32px;top:186px">LOREM IPSUM</h3>
  <ul class="bullets" style="left:32px;top:214px">
    <li><svg class="tick"><use href="#tick"/></svg>Lorem ipsum dolor sit amet, consectetur adipiscing elit, sed do eiusmod tempor incididunt</li>
    <li><svg class="tick"><use href="#tick"/></svg>Lorem ipsum dolor sit amet, consectetur adipiscing elit, sed do eiusmod tempor incididunt</li>
    <li><svg class="tick"><use href="#tick"/></svg>Lorem ipsum dolor sit amet, consectetur adipiscing elit, sed do eiusmod tempor incididunt</li>
    <li><svg class="tick"><use href="#tick"/></svg>Lorem ipsum dolor sit amet, consectetur adipiscing elit, sed do eiusmod tempor incididunt</li>
  </ul>
  <h3 class="section-head" style="left:32px;top:357px">LOREM IPSUM</h3>
  <ul class="bullets" style="left:32px;top:385px">
    <li><svg class="tick"><use href="#tick"/></svg>Lorem ipsum dolor sit amet, consectetur adipiscing elit, sed do eiusmod tempor incididunt</li>
    <li><svg class="tick"><use href="#tick"/></svg>Lorem ipsum dolor sit amet, consectetur adipiscing elit, sed do eiusmod tempor incididunt</li>
    <li><svg class="tick"><use href="#tick"/></svg>Lorem ipsum dolor sit amet, consectetur adipiscing elit, sed do eiusmod tempor incididunt</li>
    <li><svg class="tick"><use href="#tick"/></svg>Lorem ipsum dolor sit amet, consectetur adipiscing elit, sed do eiusmod tempor incididunt</li>
  </ul>
  <div class="photo" style="left:527px;top:107px;width:564px;height:458px;background:linear-gradient(160deg,#e6ecf1 0%,#cfd8e0 45%,#9aa4ad 75%,#b89a74 100%);border:1px solid #dcdfe3" role="img" aria-label="Photograph of three colleagues in a meeting at an office table"></div>
  <p class="footnote"><sup>*</sup>Lorem ipsum dolor sit amet, consectetur adipiscing elit, sed do eiusmod tempor incididunt ut labore et dolore magna aliqua.<br>Ut enim ad minim veniam, quis nostrud exercitation ullamco laboris</p>
</section>

<!-- Bar charts -->
<section class="slide charts">
  <div class="top-bar"></div>
  <div class="brand-tab"><div class="wordmark">HOLLOWAY<br>ENGINES</div></div>
  <h2 class="slide-title">LOREM IPSUM</h2>
  <p class="slide-subtitle">LOREM IPSUM DOLOR SIT AMET</p>
  <ul class="bullets" style="left:88px;top:125px">
    <li><svg class="tick"><use href="#tick"/></svg>Lorem ipsum dolor sit amet, consectetur adipiscing elit, sed do eiusmod tempor incididunt</li>
    <li><svg class="tick"><use href="#tick"/></svg>Lorem ipsum dolor sit amet, consectetur adipiscing elit, sed do eiusmod tempor incididunt</li>
    <li><svg class="tick"><use href="#tick"/></svg>Lorem ipsum dolor sit amet, consectetur adipiscing elit, sed do eiusmod tempor incididunt</li>
    <li><svg class="tick"><use href="#tick"/></svg>Lorem ipsum dolor sit amet, consectetur adipiscing elit, sed do eiusmod tempor incididunt</li>
  </ul>
  <ul class="bullets" style="left:589px;top:125px">
    <li><svg class="tick"><use href="#tick"/></svg>Lorem ipsum dolor sit amet, consectetur adipiscing elit, sed do eiusmod tempor incididunt</li>
    <li><svg class="tick"><use href="#tick"/></svg>Lorem ipsum dolor sit amet, consectetur adipiscing elit, sed do eiusmod tempor incididunt</li>
    <li><svg class="tick"><use href="#tick"/></svg>Lorem ipsum dolor sit amet, consectetur adipiscing elit, sed do eiusmod tempor incididunt</li>
  </ul>

  <div class="chart-card" style="left:62px">
    <div class="chart-title">Title of Barchart</div>
    <svg width="492" height="294" viewBox="0 0 492 294" font-family="Lato, sans-serif" font-size="7" fill="#555">
      <g stroke="#e2e4e8" stroke-width="1">
        <line x1="74" y1="51" x2="440" y2="51"/><line x1="74" y1="73" x2="440" y2="73"/><line x1="74" y1="95" x2="440" y2="95"/><line x1="74" y1="117" x2="440" y2="117"/><line x1="74" y1="139" x2="440" y2="139"/><line x1="74" y1="161" x2="440" y2="161"/><line x1="74" y1="183" x2="440" y2="183"/><line x1="74" y1="205" x2="440" y2="205"/>
      </g>
      <g text-anchor="end"><text x="70" y="53">800</text><text x="70" y="75">700</text><text x="70" y="97">600</text><text x="70" y="119">500</text><text x="70" y="141">400</text><text x="70" y="163">300</text><text x="70" y="185">200</text><text x="70" y="207">100</text><text x="70" y="229">0</text></g>
      <g fill="#0f2b57" stroke="#fff" stroke-width="1">
        <rect x="74" y="216" width="24.4" height="11"/><rect x="98.4" y="203" width="24.4" height="24"/><rect x="122.8" y="209" width="24.4" height="18"/><rect x="147.2" y="176" width="24.4" height="51"/><rect x="171.6" y="128" width="24.4" height="99"/><rect x="196" y="89" width="24.4" height="138"/><rect x="220.4" y="71" width="24.4" height="156"/><rect x="244.8" y="115" width="24.4" height="112"/><rect x="269.2" y="121" width="24.4" height="106"/><rect x="293.6" y="126" width="24.4" height="101"/><rect x="318" y="183" width="24.4" height="44"/><rect x="342.4" y="176" width="24.4" height="51"/><rect x="366.8" y="183" width="24.4" height="44"/><rect x="391.2" y="218" width="24.4" height="9"/><rect x="415.6" y="205" width="24.4" height="22"/>
      </g>
      <line x1="74" y1="227" x2="440" y2="227" stroke="#888"/>
      <g font-size="6.5">
        <text transform="translate(86 236) rotate(-40)" text-anchor="end">10, 20</text><text transform="translate(110 236) rotate(-40)" text-anchor="end">20, 30</text><text transform="translate(135 236) rotate(-40)" text-anchor="end">30, 40</text><text transform="translate(159 236) rotate(-40)" text-anchor="end">40, 50</text><text transform="translate(184 236) rotate(-40)" text-anchor="end">50, 60</text><text transform="translate(208 236) rotate(-40)" text-anchor="end">60, 70</text><text transform="translate(232 236) rotate(-40)" text-anchor="end">70, 80</text><text transform="translate(257 236) rotate(-40)" text-anchor="end">80, 90</text><text transform="translate(281 236) rotate(-40)" text-anchor="end">90, 100</text><text transform="translate(306 236) rotate(-40)" text-anchor="end">100, 110</text><text transform="translate(330 236) rotate(-40)" text-anchor="end">110, 120</text><text transform="translate(354 236) rotate(-40)" text-anchor="end">120, 130</text><text transform="translate(379 236) rotate(-40)" text-anchor="end">130, 140</text><text transform="translate(403 236) rotate(-40)" text-anchor="end">140, 150</text><text transform="translate(428 236) rotate(-40)" text-anchor="end">150, 160</text>
      </g>
    </svg>
  </div>

  <div class="chart-card" style="left:577px">
    <div class="chart-title">Title of second Barchart</div>
    <svg width="492" height="294" viewBox="0 0 492 294" font-family="Lato, sans-serif" font-size="7" fill="#555">
      <g stroke="#e2e4e8" stroke-width="1">
        <line x1="74" y1="51" x2="440" y2="51"/><line x1="74" y1="73" x2="440" y2="73"/><line x1="74" y1="95" x2="440" y2="95"/><line x1="74" y1="117" x2="440" y2="117"/><line x1="74" y1="139" x2="440" y2="139"/><line x1="74" y1="161" x2="440" y2="161"/><line x1="74" y1="183" x2="440" y2="183"/><line x1="74" y1="205" x2="440" y2="205"/>
      </g>
      <g text-anchor="end"><text x="70" y="53">800</text><text x="70" y="75">700</text><text x="70" y="97">600</text><text x="70" y="119">500</text><text x="70" y="141">400</text><text x="70" y="163">300</text><text x="70" y="185">200</text><text x="70" y="207">100</text><text x="70" y="229">0</text></g>
      <g fill="#0f2b57" stroke="#fff" stroke-width="1">
        <rect x="74" y="216" width="24.4" height="11"/><rect x="98.4" y="203" width="24.4" height="24"/><rect x="122.8" y="209" width="24.4" height="18"/><rect x="147.2" y="176" width="24.4" height="51"/><rect x="171.6" y="128" width="24.4" height="99"/><rect x="196" y="89" width="24.4" height="138"/><rect x="220.4" y="71" width="24.4" height="156"/><rect x="244.8" y="115" width="24.4" height="112"/><rect x="269.2" y="121" width="24.4" height="106"/><rect x="293.6" y="126" width="24.4" height="101"/><rect x="318" y="183" width="24.4" height="44"/><rect x="342.4" y="176" width="24.4" height="51"/><rect x="366.8" y="183" width="24.4" height="44"/><rect x="391.2" y="218" width="24.4" height="9"/><rect x="415.6" y="205" width="24.4" height="22"/>
      </g>
      <line x1="74" y1="227" x2="440" y2="227" stroke="#888"/>
      <g font-size="6.5">
        <text transform="translate(86 236) rotate(-40)" text-anchor="end">10, 20</text><text transform="translate(110 236) rotate(-40)" text-anchor="end">20, 30</text><text transform="translate(135 236) rotate(-40)" text-anchor="end">30, 40</text><text transform="translate(159 236) rotate(-40)" text-anchor="end">40, 50</text><text transform="translate(184 236) rotate(-40)" text-anchor="end">50, 60</text><text transform="translate(208 236) rotate(-40)" text-anchor="end">60, 70</text><text transform="translate(232 236) rotate(-40)" text-anchor="end">70, 80</text><text transform="translate(257 236) rotate(-40)" text-anchor="end">80, 90</text><text transform="translate(281 236) rotate(-40)" text-anchor="end">90, 100</text><text transform="translate(306 236) rotate(-40)" text-anchor="end">100, 110</text><text transform="translate(330 236) rotate(-40)" text-anchor="end">110, 120</text><text transform="translate(354 236) rotate(-40)" text-anchor="end">120, 130</text><text transform="translate(379 236) rotate(-40)" text-anchor="end">130, 140</text><text transform="translate(403 236) rotate(-40)" text-anchor="end">140, 150</text><text transform="translate(428 236) rotate(-40)" text-anchor="end">150, 160</text>
      </g>
    </svg>
  </div>
  <p class="footnote"><sup>*</sup>Lorem ipsum dolor sit amet, consectetur adipiscing elit, sed do eiusmod tempor incididunt ut labore et dolore magna aliqua.<br>Ut enim ad minim veniam, quis nostrud exercitation ullamco laboris</p>
</section>

<!-- Line chart with text -->
<section class="slide lines">
  <div class="top-bar"></div>
  <div class="brand-tab"><div class="wordmark">HOLLOWAY<br>ENGINES</div></div>
  <h2 class="slide-title">LOREM IPSUM</h2>
  <p class="slide-subtitle">LOREM IPSUM DOLOR SIT AMET</p>
  <svg style="position:absolute;left:40px;top:190px" width="520" height="290" viewBox="0 0 520 290" font-family="Lato, sans-serif" font-size="8" fill="#555">
    <g text-anchor="end">
      <text x="48" y="13">6.E+07</text><text x="48" y="40">5.E+07</text><text x="48" y="67">5.E+07</text><text x="48" y="94">4.E+07</text><text x="48" y="121">4.E+07</text><text x="48" y="148">3.E+07</text><text x="48" y="175">3.E+07</text><text x="48" y="202">2.E+07</text><text x="48" y="229">2.E+07</text><text x="48" y="256">1.E+07</text>
    </g>
    <line x1="54" y1="8" x2="54" y2="253" stroke="#666"/>
    <line x1="54" y1="253" x2="510" y2="253" stroke="#666"/>
    <g text-anchor="middle"><text x="92" y="266">2010</text><text x="202" y="266">2013</text><text x="312" y="266">2016</text><text x="422" y="266">2019</text></g>
    <polyline fill="none" stroke="#9fc0ae" stroke-width="2" points="56,230 70,224 84,220 96,212 110,200 124,192 138,182 152,175 166,170 180,162 194,155 208,152 222,148 236,140 250,134 264,130 278,124 292,116 306,102 320,92 334,84 348,74 362,66 376,58 390,52 404,46 418,44 432,42 446,38 460,36 474,34 488,30 500,26"/>
    <polyline fill="none" stroke="#5f86b5" stroke-width="1.5" points="56,232 70,226 84,222 96,216 110,204 124,196 138,186 152,180 166,174 180,166 194,160 208,156 222,152 236,144 250,138 264,134 278,128 292,120 306,106 320,96 334,88 348,78 362,70 376,62 390,56 404,50 418,46 432,44 446,40 460,38 474,36 488,32 500,28"/>
    <polyline fill="none" stroke="#0f2b57" stroke-width="1.5" points="56,234 70,229 84,225 96,219 110,208 124,200 138,191 152,185 166,179 180,172 194,166 208,161 222,157 236,149 250,143 264,139 278,132 292,123 306,109 320,99 334,91 348,81 362,73 376,65 390,58 404,52 418,48 432,46 446,42 460,40 474,38 488,34 500,29"/>
  </svg>
  <h3 class="section-head" style="left:604px;top:180px">LOREM IPSUM</h3>
  <p class="body-copy" style="top:212px">Lorem ipsum dolor sit amet, consectetur adipiscing elit, sed do eiusmod tempor incididunt ut labore et dolore magna aliqua. Ut enim ad minim veniam, quis nostrud exercitation ullamco laboris nisi ut aliquip ex ea commodo consequat. Duis aute irure dolor in reprehenderit in voluptate velit esse cillum dolore eu fugiat nulla pariatur. Excepteur sint occaecat cupidatat non proident.</p>
  <h3 class="section-head" style="left:604px;top:339px">LOREM IPSUM</h3>
  <p class="body-copy" style="top:371px">Lorem ipsum dolor sit amet, consectetur adipiscing elit, sed do eiusmod tempor incididunt ut labore et dolore magna aliqua. Ut enim ad minim veniam, quis nostrud exercitation ullamco laboris nisi ut aliquip ex ea commodo consequat. Duis aute irure dolor in reprehenderit in voluptate velit esse cillum dolore eu fugiat nulla pariatur. Excepteur sint occaecat cupidatat non proident.</p>
  <p class="footnote"><sup>*</sup>Lorem ipsum dolor sit amet, consectetur adipiscing elit, sed do eiusmod tempor incididunt ut labore et dolore magna aliqua.<br>Ut enim ad minim veniam, quis nostrud exercitation ullamco laboris</p>
</section>

<!-- Closing -->
<section class="slide closing">
  <div class="photo" role="img" aria-label="Dark image of financial market charts over a night city skyline"></div>
  <div class="top-bar"></div>
  <div class="brand-tab"><div class="wordmark">HOLLOWAY<br>ENGINES</div></div>
  <h2 class="thanks">THANK YOU</h2>
  <p class="footnote light"><sup>*</sup>Lorem ipsum dolor sit amet, consectetur adipiscing elit, sed do eiusmod tempor incididunt ut labore et dolore magna aliqua.<br>Ut enim ad minim veniam, quis nostrud exercitation ullamco laboris</p>
</section>

</body>
</html>
```